Design the packaging for a wholesale/retail Date fruit company

We need a box designed for a dates fruit box. This will be used for the wholesale packaging. The brand is called Zahwan Dates , it is a new business. Zahwan means the home. It will be part of a food exporting business called Zahwan Foods. It will be based out of the Middle East and the Holy Lands. Recently Qatar had a desert games and one of their stadiums was also called Zahwan, it was designed to represent an Arabian tent. The logo hasn't been designed yet but something simple is fine. I also have a sample design, you can use most of the information from. The product is a Product of Palestine, it is in 5kg boxes the nutritional information is on the sample.

The company is called Hadi Nasrallah General Trading (Hadi Nasrallah General Trading) based in Doha Qatar. Logo is provided.

The exporter details are on the sample box.
Use this companies packaging as inspiration for what we are looking to compete with https://morvane-example.com/

I require the illustrator/photoshop files please so that we can update details on it.

Industry/Entity Type

food (dates)

Requirements
Must have
• English & Arabic text
Nice to have
• try and incorporate the colour CFB53B

```html
<!DOCTYPE html>
<html lang="en">
<head>
<meta charset="utf-8">
<title>Zahwan Dates – Medjool Dates 5 kg box</title>
<link href="https://fonts.googleapis.com/css2?family=Aref+Ruqaa:wght@700&family=Montserrat:wght@300;400;700&family=Noto+Kufi+Arabic:wght@400&family=Playfair+Display:ital,wght@1,700&family=Ubuntu:wght@500&display=swap" rel="stylesheet">
<style>
:root{
  --cream:#f7e6a4;
  --brown:#4b3022;
  --gold:#cfb53b;
  --gold-light:#e4cf8a;
  --ink:#5a4638;
  --paper:#ffffff;
}
*{margin:0;padding:0;box-sizing:border-box}
html,body{width:1200px;height:972px;overflow:hidden;background:var(--paper)}
.box{position:relative;width:1200px;height:972px}
.dieline{position:absolute;inset:0}
.t{position:absolute;white-space:nowrap;transform-origin:center center}
.flip{transform:translate(-50%,-50%) rotate(180deg)}
.mid{transform:translate(-50%,-50%)}
.down{transform:translate(-50%,-50%) rotate(90deg)}
.up{transform:translate(-50%,-50%) rotate(-90deg)}
.ar{direction:rtl;unicode-bidi:isolate}
.line{display:block}

.brand-ar{font-family:"Aref Ruqaa",serif;font-weight:700;color:var(--gold-light);font-size:54px;line-height:1}
.brand-en{font-family:"Ubuntu",sans-serif;font-weight:500;color:var(--gold-light);font-size:22px}
.claim{font-family:"Montserrat",sans-serif;font-weight:300;color:var(--ink);font-size:21px;line-height:1.2}
.claim-ar{font-family:"Noto Kufi Arabic",sans-serif;font-weight:400;color:var(--ink);font-size:19px;line-height:1.35;text-align:center}
.product{font-family:"Playfair Display",serif;font-style:italic;font-weight:700;color:var(--gold-light);font-size:54px}
.product-ar{font-family:"Noto Kufi Arabic",sans-serif;font-weight:400;color:var(--gold-light);font-size:22px}
.weight{font-family:"Montserrat",sans-serif;font-weight:300;color:var(--gold);font-size:19px;letter-spacing:.5px}

.origin{font-family:"Montserrat",sans-serif;font-weight:300;color:var(--ink);font-size:17px}
.origin-ar{font-family:"Noto Kufi Arabic",sans-serif;font-weight:400;color:var(--ink);font-size:14px}

.nutrition{position:absolute;left:128px;top:293px;width:150px;transform:translate(-50%,-50%) rotate(90deg);font-family:"Montserrat",sans-serif;font-size:5px;color:var(--ink)}
.nutrition table{width:100%;border-collapse:collapse;background:var(--paper)}
.nutrition th{background:var(--brown);color:var(--cream);font-weight:400;text-align:left;padding:1px 2px}
.nutrition td{border:0.5px solid var(--ink);padding:0.5px 2px;height:8.5px}
.nutrition .ar-cell{direction:rtl;text-align:right;font-family:"Noto Kufi Arabic",sans-serif}
.nutrition .note{margin-top:2px;font-size:4.5px}

.dates-box{position:absolute;left:103px;top:613px;width:63px;height:132px;background:var(--paper)}
.dates-fields{left:134px;top:679px;width:132px;font-family:"Montserrat",sans-serif;font-size:7px;color:var(--ink);line-height:2.2}
.storage{left:78px;top:688px;font-family:"Montserrat",sans-serif;font-size:7px;color:var(--ink);text-align:center;line-height:1.5}

.side-brand-ar{font-family:"Aref Ruqaa",serif;font-weight:700;color:var(--brown);font-size:38px;line-height:1}
.side-brand-en{font-family:"Ubuntu",sans-serif;font-weight:500;color:var(--brown);font-size:17px}
.contact{font-family:"Montserrat",sans-serif;color:var(--brown);font-size:10px}
.contact.bold{font-weight:700;font-size:9px}
.trader{font-family:"Montserrat",sans-serif;font-weight:400;color:var(--brown);font-size:21px;line-height:1.25;text-align:center}
</style>
</head>
<body>
<div class="box">
  <svg class="dieline" width="1200" height="972" viewBox="0 0 1200 972" xmlns="http://www.w3.org/2000/svg">
    <g role="img" aria-label="Cream damask ornamental pattern covering the box">
      <polygon fill="var(--cream)" points="206,14 995,14 995,955 206,955"/>
      <polygon fill="var(--cream)" points="206,26 40,26 42,175 31,185 31,780 40,790 38,948 206,948 206,795 196,788 206,780 206,185 196,177 206,168"/>
      <polygon fill="var(--cream)" points="995,26 1162,26 1160,175 1170,185 1170,780 1160,790 1162,948 995,948 995,795 1005,788 995,780 995,185 1005,177 995,168"/>
    </g>
    <rect x="493" y="16" width="215" height="938" fill="var(--brown)"/>
    <line x1="503" y1="16" x2="503" y2="954" stroke="var(--gold)" stroke-width="1"/>
    <line x1="698" y1="16" x2="698" y2="954" stroke="var(--gold)" stroke-width="1"/>
    <ellipse cx="600" cy="482" rx="221" ry="125" fill="var(--brown)"/>
    <rect x="416" y="376" width="368" height="214" fill="var(--brown)"/>
    <path d="M428 416 L428 386 L480 386 Q600 355 720 386 L772 386 L772 416 Q812 482 772 548 L772 578 L720 578 Q600 610 480 578 L428 578 L428 548 Q388 482 428 416 Z" fill="none" stroke="var(--gold)" stroke-width="1"/>
    <g fill="none" stroke="var(--brown)" stroke-width="1.6">
      <path d="M346 207 H255 M223 240 V330"/>
      <path d="M859 207 H950 M982 240 V330"/>
      <path d="M346 770 H255 M223 737 V645"/>
      <path d="M859 770 H950 M982 737 V645"/>
    </g>
    <g role="img" aria-label="Scroll corner ornaments" fill="var(--brown)" opacity="0.85">
      <circle cx="235" cy="219" r="10"/><circle cx="970" cy="219" r="10"/>
      <circle cx="235" cy="758" r="10"/><circle cx="970" cy="758" r="10"/>
    </g>
    <line x1="1102" y1="550" x2="1102" y2="572" stroke="var(--brown)" stroke-width="0.8"/>
    <line x1="1102" y1="736" x2="1102" y2="756" stroke="var(--brown)" stroke-width="0.8"/>
  </svg>

  <!-- top lid (reads upside down) -->
  <div class="t flip brand-en" style="left:600px;top:59px">Zahwan Dates</div>
  <div class="t flip brand-ar ar" style="left:600px;top:110px">تمور زهوان</div>
  <div class="t flip claim-ar" style="left:385px;top:120px"><span class="line">100% <span class="ar">طبيعي</span></span><span class="line ar">جودة فاخرة</span></div>
  <div class="t flip claim" style="left:817px;top:120px">100%NATURAL<br>Premium Quality</div>

  <!-- front panel -->
  <div class="t mid brand-ar ar" style="left:600px;top:243px">تمور زهوان</div>
  <div class="t mid brand-en" style="left:600px;top:296px">Zahwan Dates</div>
  <div class="t mid product" style="left:600px;top:474px">Medjool Dates</div>
  <div class="t mid product-ar ar" style="left:600px;top:532px">تمر مجول فلسطيني</div>
  <div class="t mid weight" style="left:600px;top:737px">5 Kg/ 11 LBS NET</div>
  <div class="t mid brand-ar ar" style="left:600px;top:843px">تمور زهوان</div>
  <div class="t mid brand-en" style="left:600px;top:898px">Zahwan Dates</div>
  <div class="t mid claim" style="left:388px;top:845px">100%NATURAL<br>Premium Quality</div>
  <div class="t mid claim-ar" style="left:820px;top:843px"><span class="line">100% <span class="ar">طبيعي</span></span><span class="line ar">جودة فاخرة</span></div>

  <!-- left flap -->
  <div class="nutrition">
    <table>
      <tr><th colspan="2">Nutrition facts<br>Serving Size (100 g)</th><th class="ar-cell">القيمة الغذائية<br>الحجم المقدم (100 غ)</th></tr>
      <tr><td>Energy (KCAL)</td><td>268</td><td class="ar-cell">طاقة</td></tr>
      <tr><td>Carbohydrate (g)</td><td>64</td><td class="ar-cell">كربوهيدرات</td></tr>
      <tr><td>Protein (g)</td><td>2</td><td class="ar-cell">بروتين</td></tr>
      <tr><td>Fat (g)</td><td>0</td><td class="ar-cell">دهن</td></tr>
      <tr><td>Sodium (mg)</td><td>0</td><td class="ar-cell">صوديوم</td></tr>
      <tr><td>Cholesterol (g)</td><td>0</td><td class="ar-cell">كولسترول</td></tr>
      <tr><td>Dietary Fibers (g)</td><td>6</td><td class="ar-cell">الألياف الغذائية</td></tr>
      <tr><td>Iron (mg)</td><td>2</td><td class="ar-cell">الحديد</td></tr>
      <tr><td>Magnesium (mg)</td><td>35</td><td class="ar-cell">المغنيسيوم</td></tr>
      <tr><td>Potassium (mg)</td><td>650</td><td class="ar-cell">البوتاسيوم</td></tr>
    </table>
    <div class="note">Fresh Natural Medjool Dates which includes Pits</div>
    <div class="note ar">تمر مجول طبيعي يحتوي على نواة</div>
  </div>
  <div class="t down origin" style="left:142px;top:492px">Produce of Palestine</div>
  <div class="t down origin-ar ar" style="left:115px;top:488px">إنتاج فلسطين</div>
  <div class="dates-box"></div>
  <div class="t down dates-fields">
    <span class="line">PRO :</span><span class="line">EXP :</span><span class="line ar">تاريخ الإنتاج والانتهاء</span>
  </div>
  <div class="t down storage"><span class="line ar">تحفظ في مكان بارد وجاف</span><span class="line">Store in Cool &amp; Dry Place</span></div>

  <!-- right flap -->
  <div class="t up side-brand-ar ar" style="left:1043px;top:284px">تمور زهوان</div>
  <div class="t up side-brand-en" style="left:1080px;top:284px">Zahwan Dates</div>
  <div class="t up contact" style="left:1108px;top:282px">info@zahwandates.example</div>
  <div class="t up contact" style="left:1125px;top:282px">www.zahwandates.example</div>
  <div class="t up trader" style="left:1062px;top:654px">Hadi Nasrallah<br>General Trading</div>
  <div class="t up contact bold" style="left:1121px;top:654px">sales@hngtrading.example</div>
  <div class="t up contact bold" style="left:1136px;top:654px">www.hngtrading.example</div>
</div>
</body>
</html>
```